Updated DJ business Card showing other businesses

DJ Talbo offers professional mobile dj services including DJ. MC. Karaoke.
Silent Disco (will attach logo)
I also offer a 360 Photo Booth.

Contact info:
(405) 555-0147
mark.fenstell@pelimail.com
Social Media @DJTalboOKC

```html
<!DOCTYPE html>
<html lang="en">
<head>
<meta charset="utf-8">
<title>DJ Talbo — Business Card</title>
<link href="https://fonts.googleapis.com/css2?family=Anton&family=Lato:wght@400;700;900&family=Titillium+Web:ital,wght@0,700;1,700&display=swap" rel="stylesheet">
<style>
  :root {
    --bg: #2b2b2d;
    --card: #0b0b0c;
    --white: #ffffff;
    --red: #d6224a;
    --grey: #9a9a9e;
  }
  * { box-sizing: border-box; margin: 0; padding: 0; }
  html, body { width: 1200px; height: 900px; overflow: hidden; background: var(--bg); }
  .canvas { position: relative; width: 1200px; height: 900px; }

  .card {
    position: absolute; left: 250px; width: 700px; height: 400px;
    background: var(--card); border-radius: 22px; overflow: hidden;
    box-shadow: 0 14px 30px rgba(0,0,0,.45);
  }
  .card--front { top: 35px; }
  .card--back { top: 465px; }

  /* Front */
  .front-logo {
    position: absolute; top: 92px; left: 0; right: 0; text-align: center;
    font-family: "Anton", sans-serif; font-size: 118px; line-height: 1;
    color: var(--white); letter-spacing: 2px;
  }
  .front-services {
    position: absolute; top: 258px; left: 0; right: 0; text-align: center;
    font-family: "Titillium Web", sans-serif; font-weight: 700; font-size: 27px;
    color: var(--white); letter-spacing: 1px;
  }
  .front-extra {
    position: absolute; top: 300px; left: 0; right: 0; text-align: center;
    font-family: "Titillium Web", sans-serif; font-style: italic; font-weight: 700;
    font-size: 17px; color: var(--white); letter-spacing: 1.5px;
  }

  /* Back */
  .back-art { position: absolute; inset: 0; }
  .back-copy { position: absolute; left: 34px; top: 34px; width: 380px; }
  .offer {
    font-family: "Anton", sans-serif; font-size: 30px; line-height: 1.08;
    color: var(--white); text-transform: uppercase; letter-spacing: .5px;
  }
  .offer-list {
    margin-top: 6px; font-family: "Lato", sans-serif; font-weight: 700;
    font-size: 26px; color: var(--red);
  }
  .partner-badge {
    margin-top: 8px; width: 110px; height: 38px; border-radius: 19px;
    border: 2px solid var(--grey); background: #1c1c1e;
  }
  .contacts { position: absolute; left: 34px; top: 272px; font-family: "Lato", sans-serif; color: var(--white); }
  .contact { display: flex; align-items: center; gap: 10px; line-height: 1.3; }
  .contact svg { flex: none; }
  .contact--phone { font-weight: 900; font-size: 24px; }
  .contact--mail, .contact--web { font-size: 17px; }
  .contact--social { margin-top: 12px; font-weight: 700; font-size: 20px; }
  .dot { width: 14px; height: 14px; border-radius: 50%; background: var(--red); flex: none; }
</style>
</head>
<body>
<main class="canvas">

  <section class="card card--front" aria-label="Card front">
    <div class="front-logo">DJ TALBO</div>
    <p class="front-services">DJ | MC | KARAOKE | SILENT DISCO</p>
    <p class="front-extra">I ALSO OFFER A 360 PHOTO BOOTH.</p>
  </section>

  <section class="card card--back" aria-label="Card back">
    <svg class="back-art" width="700" height="400" viewBox="0 0 700 400">
      <defs>
        <linearGradient id="mascotFill" x1="0" y1="0" x2="1" y2="0">
          <stop offset="0" stop-color="#ffffff"/>
          <stop offset=".45" stop-color="#8d8d90"/>
          <stop offset="1" stop-color="#141416"/>
        </linearGradient>
      </defs>
      <path class="red-band" d="M560 0 Q700 150 640 400 L700 400 L700 0 Z" fill="var(--red)"/>
      <path d="M470 0 Q640 120 610 400 L640 400 Q700 150 560 0 Z" fill="#111113"/>
      <path role="img" aria-label="Large brand mascot illustration in white-to-black gradient"
            d="M360 400 Q400 250 420 140 Q470 60 560 20 Q640 130 615 400 Z" fill="url(#mascotFill)"/>
    </svg>

    <div class="back-copy">
      <p class="offer">DJ Talbo offers<br>professional mobile dj<br>services including</p>
      <p class="offer-list">DJ. MC. Karaoke.</p>
      <div class="partner-badge" role="img" aria-label="Silent Disco partner badge"></div>
    </div>

    <div class="contacts">
      <p class="contact contact--phone">
        <svg width="18" height="18" viewBox="0 0 24 24"><path d="M6.6 10.8a15 15 0 0 0 6.6 6.6l2.2-2.2a1 1 0 0 1 1-.25 11.4 11.4 0 0 0 3.6.57 1 1 0 0 1 1 1V20a1 1 0 0 1-1 1A17 17 0 0 1 3 4a1 1 0 0 1 1-1h3.5a1 1 0 0 1 1 1c0 1.25.2 2.45.57 3.57a1 1 0 0 1-.25 1Z" fill="var(--red)"/></svg>
        (405) 555-0147
      </p>
      <p class="contact contact--mail">
        <svg width="18" height="14" viewBox="0 0 18 14"><rect x="0" y="0" width="18" height="14" rx="2" fill="var(--red)"/><path d="M1 1.5 9 8l8-6.5" stroke="#0b0b0c" stroke-width="1.6" fill="none"/></svg>
        mark.fenstell@pelimail.com
      </p>
      <p class="contact contact--web">
        <svg width="18" height="18" viewBox="0 0 18 18"><circle cx="9" cy="9" r="8" fill="none" stroke="var(--red)" stroke-width="2"/><path d="M1 9h16M9 1c3 3 3 13 0 16M9 1c-3 3-3 13 0 16" stroke="var(--red)" stroke-width="1.4" fill="none"/></svg>
        www.dj-talbo.com
      </p>
      <p class="contact contact--social"><span class="dot"></span>@DJTalboOKC</p>
    </div>
  </section>

</main>
</body>
</html>
```